Redesign Website - Current one too plain

The description is in the uploaded file. Please let me know if you need any more information. I'd prefer it if someone could implement the design to a WordPress site but the best design will win, regardless.
I would like the forms to look nice as well
UPDATE:
I don't think we can use the images that I provided, I think they make the site look a bit 'cheap' and I really don't know how to replace them. One thought I have had is to make the "Simple, Unique, Effective" a second feature on the right side of the page with the search on the left
Target Market(s)
Small companies, private sellers of cars and people who rent their caravan/holiday home out
Industry/Entity Type
Advertising
Number of Pages Required
3 page
Colors
Designer to choose colors to be used in the design.
Look and feel
Each slider illustrates characteristics of the customer's brand and the style your logo design should communicate.

```html
<!DOCTYPE html>
<html lang="en">
<head>
<meta charset="utf-8">
<title>KORVA – Find a business by its code</title>
<link rel="stylesheet" href="https://fonts.googleapis.com/css2?family=Outfit:wght@300;400;500;600;700;800;900&display=swap">
<style>
  :root {
    --ink: #111111;
    --ink-soft: #2b2b2b;
    --muted: #6a6a6a;
    --rule: #b9b9b9;
    --lime: #e4ff00;
    --panel: #f3f3f3;
    --paper: #ffffff;
    --chev: #8a8a8a;
  }
  * { margin: 0; padding: 0; box-sizing: border-box; }
  html, body { width: 1200px; height: 1190px; overflow: hidden; background: var(--paper); }
  body { font-family: "Outfit", sans-serif; color: var(--ink); position: relative; }

  .brand { position: absolute; left: 89px; top: 42px; display: flex; align-items: center; gap: 10px; }
  .brand-dot { width: 30px; height: 30px; border-radius: 50%; background: var(--ink-soft); }
  .brand-name { font-size: 30px; font-weight: 400; letter-spacing: 4px; color: var(--ink-soft); }

  .nav a { position: absolute; top: 50px; font-size: 16px; font-weight: 500; color: var(--ink); text-decoration: none; }
  .btn-login { position: absolute; left: 978px; top: 40px; width: 133px; height: 44px; border-radius: 8px;
    background: var(--ink-soft); color: #fff; font-size: 16px; font-weight: 500;
    display: flex; align-items: center; justify-content: center; }

  .chevron { position: absolute; width: 34px; height: 20px; }
  .code-char { position: absolute; top: 214px; font-family: "Outfit", sans-serif; font-weight: 800;
    font-size: 312px; line-height: 1; color: #000; white-space: nowrap; }
  .code-char-letter { left: 84px; width: 205px; text-align: center; }
  .code-char-digit { left: 290px; width: 120px; text-align: right; }

  .categories { position: absolute; left: 467px; top: 270px; width: 122px; list-style: none; }
  .categories li { font-size: 27px; font-weight: 500; height: 81px; padding-top: 4px; border-bottom: 1.5px solid var(--rule); white-space: nowrap; }
  .categories li:last-child { border-bottom: none; }

  .btn-search { position: absolute; left: 88px; top: 636px; width: 151px; height: 45px; border-radius: 8px;
    background: var(--lime); font-size: 21px; font-weight: 500; display: flex; align-items: center; justify-content: center; }
  .link-advertise { position: absolute; left: 260px; top: 644px; font-size: 21px; font-weight: 500; color: var(--ink); text-decoration: underline; text-underline-offset: 3px; }

  .showcase { position: absolute; border: 4px solid var(--lime); }
  .slide-1 { left: 754px; top: 164px; width: 270px; height: 458px; border-radius: 135px;
    background: linear-gradient(180deg, #a9c3e0 0%, #c46a3e 35%, #efefef 60%, #9a9389 100%); }
  .slide-2 { left: 1056px; top: 161px; width: 270px; height: 459px; border-radius: 135px;
    background: linear-gradient(180deg, #86b6e8 0%, #cfd6dd 40%, #a8b3bd 70%, #9aa85a 100%); }

  .pager { position: absolute; left: 853px; top: 646px; display: flex; align-items: center; gap: 10px; font-size: 12px; font-weight: 500; }

  .features { position: absolute; left: 89px; top: 774px; width: 1022px; height: 273px; background: var(--panel); border-radius: 24px; }
  .feature-card-active { position: absolute; left: 416px; top: 807px; width: 316px; height: 209px; background: var(--paper); border-radius: 22px; }
  .feature { position: absolute; top: 828px; }
  .feature svg { width: 44px; height: 44px; }
  .feature h2 { margin-top: 18px; font-size: 33px; font-weight: 700; }
  .feature p { margin-top: 12px; font-size: 17px; font-weight: 400; line-height: 26px; color: var(--muted); }

  .footer { position: absolute; left: 0; top: 1146px; width: 1196px; border-top: 1.5px solid #8d8d8d; text-align: center; padding-top: 12px; font-size: 19px; }
  .footer strong { font-weight: 700; }
</style>
</head>
<body>

<header>
  <div class="brand"><span class="brand-dot"></span><span class="brand-name">KORVA</span></div>
  <nav class="nav">
    <a href="#" style="left:547px">Home</a>
    <a href="#" style="left:647px">Advistise</a>
    <a href="#" style="left:769px">Contact</a>
    <a href="#" style="left:881px">Register</a>
  </nav>
  <div class="btn-login">Login</div>
</header>

<main>
  <svg class="chevron" style="left:159px;top:171px" viewBox="0 0 34 20"><path d="M3 17 L17 4 L31 17" fill="none" stroke="var(--chev)" stroke-width="3.5"/></svg>
  <svg class="chevron" style="left:363px;top:171px" viewBox="0 0 34 20"><path d="M3 17 L17 4 L31 17" fill="none" stroke="var(--chev)" stroke-width="3.5"/></svg>
  <div class="code-char code-char-letter">A</div>
  <div class="code-char code-char-digit">1</div>
  <svg class="chevron" style="left:159px;top:552px" viewBox="0 0 34 20"><path d="M3 3 L17 16 L31 3" fill="none" stroke="var(--chev)" stroke-width="3.5"/></svg>
  <svg class="chevron" style="left:363px;top:552px" viewBox="0 0 34 20"><path d="M3 3 L17 16 L31 3" fill="none" stroke="var(--chev)" stroke-width="3.5"/></svg>

  <ul class="categories">
    <li>Car</li>
    <li>Caravan</li>
    <li>Company</li>
  </ul>

  <div class="btn-search">Search</div>
  <a class="link-advertise" href="#">Advertise your Company</a>

  <div class="showcase slide-1" role="img" aria-label="White SUV parked in front of red rock formations"></div>
  <div class="showcase slide-2" role="img" aria-label="Front of a white touring caravan on grass"></div>

  <div class="pager">
    <svg width="12" height="10" viewBox="0 0 12 10"><path d="M11 5 H2 M5 1 L1 5 L5 9" fill="none" stroke="var(--muted)" stroke-width="1.2"/></svg>
    <span>1/3</span>
    <svg width="12" height="10" viewBox="0 0 12 10"><path d="M1 5 H10 M7 1 L11 5 L7 9" fill="none" stroke="var(--ink)" stroke-width="1.2"/></svg>
  </div>

  <section class="features-wrap">
    <div class="features"></div>
    <div class="feature-card-active"></div>

    <div class="feature" style="left:159px">
      <svg viewBox="0 0 44 44"><circle cx="22" cy="22" r="17" fill="none" stroke="var(--ink)" stroke-width="6" stroke-dasharray="5 3"/><circle cx="22" cy="22" r="14" fill="var(--ink)"/><circle cx="22" cy="22" r="10" fill="none" stroke="#fff" stroke-width="2"/><path d="M17 22 L21 26 L27 18" fill="none" stroke="#fff" stroke-width="2.5"/></svg>
      <h2>Simple</h2>
      <p>Create your Advert and<br>display your code</p>
    </div>

    <div class="feature" style="left:445px">
      <svg viewBox="0 0 44 44"><circle cx="22" cy="20" r="17" fill="none" stroke="var(--ink)" stroke-width="6" stroke-dasharray="5 3"/><circle cx="22" cy="20" r="14" fill="var(--ink)"/><circle cx="22" cy="20" r="10" fill="none" stroke="#fff" stroke-width="2"/><path d="M22 13 L24 18 L29 18 L25 21 L27 26 L22 23 L17 26 L19 21 L15 18 L20 18 Z" fill="#fff"/><path d="M17 39 H27 M19 42 H25" stroke="var(--ink)" stroke-width="2"/></svg>
      <h2>Unique</h2>
      <p>customers find you by entering<br>your east-to-remember code</p>
    </div>

    <div class="feature" style="left:778px">
      <svg viewBox="0 0 44 44"><circle cx="22" cy="22" r="17" fill="none" stroke="var(--ink)" stroke-width="6" stroke-dasharray="5 3"/><circle cx="22" cy="22" r="14" fill="var(--ink)"/><path d="M15 21 H19 V30 H15 Z M20 21 L23 14 C25 14 25 16 25 18 H29 C30 18 30 20 29 21 L28 29 C28 30 27 30 26 30 H20 Z" fill="#fff"/></svg>
      <h2>Effective</h2>
      <p>customers are directed to you<br>and not a list of your competitors</p>
    </div>
  </section>
</main>

<footer class="footer">© 2023 <strong>KORVA</strong> . All Rights Reserved</footer>

</body>
</html>
```